Income Tax Business Cards - Updates

Need to update these business cards while keeping all the same wording but just update them and make them look nicer and more modern/ on brand with our brand.

Industry/Entity Type

finance

Contact Information for Business Card

we have multiple locations so will just need to easily be able to change the address and phone numbers

Colors

Designer to choose colors to be used in the design.

```html
<!DOCTYPE html>
<html lang="en">
<head>
<meta charset="utf-8">
<title>Northfield Tax Group – Business Card</title>
<link rel="stylesheet" href="https://fonts.googleapis.com/css2?family=Montserrat:wght@400;600;700;800&display=swap">
<style>
  :root {
    --bg: #989898;
    --green: #0e5130;
    --red: #c41e26;
    --white: #ffffff;
  }
  * { margin: 0; padding: 0; box-sizing: border-box; }
  html, body { width: 1200px; height: 1059px; overflow: hidden; }
  body { background: var(--bg); font-family: "Montserrat", sans-serif; position: relative; }

  .card {
    position: absolute;
    border-radius: 18px;
    overflow: hidden;
    background: var(--green);
    color: var(--white);
  }
  .card--front { left: 256px; top: 89px; width: 688px; height: 390px; }
  .card--back  { left: 253px; top: 569px; width: 694px; height: 394px; }

  .front-swoosh { position: absolute; inset: 0; width: 100%; height: 100%; }

  .brand-name {
    position: absolute; left: 360px; top: 110px; width: 310px;
    text-align: center; color: var(--green);
    font-weight: 700; font-size: 27px; line-height: 1.15;
  }

  .contact { position: absolute; left: 32px; top: 106px; }
  .contact__line { font-size: 18px; font-weight: 400; line-height: 26px; letter-spacing: 0.2px; }
  .contact__phone {
    display: flex; align-items: center; gap: 8px;
    margin-top: 5px; font-size: 23px; font-weight: 600;
  }
  .contact__phone svg { width: 16px; height: 16px; }

  .offer { position: absolute; left: 32px; top: 230px; }
  .offer__amount { font-size: 46px; font-weight: 700; line-height: 1; letter-spacing: 0.5px; }
  .offer__amount .accent { color: var(--red); }
  .offer__label { margin-top: 10px; font-size: 27px; font-weight: 700; line-height: 1; letter-spacing: 0.4px; }

  .footnote {
    position: absolute; left: 32px; top: 338px;
    font-size: 15px; font-weight: 600; letter-spacing: 0.2px;
    display: flex; align-items: center; gap: 8px;
  }
  .footnote__divider { width: 2px; height: 13px; background: var(--red); }

  .back-top { position: absolute; left: 0; top: 0; width: 100%; height: 202px; background: var(--green); }
  .back-rule { position: absolute; left: 0; top: 202px; width: 100%; height: 6px; background: var(--white); }
  .back-bottom { position: absolute; left: 0; top: 208px; width: 100%; bottom: 0; background: var(--red); }

  .headline { position: absolute; left: 0; width: 100%; text-align: center; font-weight: 700; line-height: 1; }
  .headline--file  { top: 42px; font-size: 74px; letter-spacing: 1px; }
  .headline--taxes { top: 113px; font-size: 74px; color: var(--red); letter-spacing: 1px; }
  .headline--amount { top: 228px; font-size: 72px; letter-spacing: 1px; }
  .headline--advance { top: 309px; font-size: 45px; letter-spacing: 0.5px; }
</style>
</head>
<body>

<section class="card card--front">
  <svg class="front-swoosh" viewBox="0 0 688 390" preserveAspectRatio="none" aria-hidden="true">
    <path d="M246 0 C250 195 440 318 688 332 L688 0 Z" fill="var(--red)"/>
    <path d="M264 0 C270 178 452 300 688 324 L688 0 Z" fill="var(--white)"/>
  </svg>

  <div class="brand-name">Northfield<br>Tax Group</div>

  <div class="contact">
    <p class="contact__line">118 Maple Grove Rd</p>
    <p class="contact__line">Ste 410</p>
    <p class="contact__line">Country Name AB 5625</p>
    <p class="contact__phone">
      <svg viewBox="0 0 24 24" aria-hidden="true"><path fill="var(--red)" d="M6.6 10.8a15.1 15.1 0 0 0 6.6 6.6l2.2-2.2a1 1 0 0 1 1-.25 11.4 11.4 0 0 0 3.6.57 1 1 0 0 1 1 1V20a1 1 0 0 1-1 1A17 17 0 0 1 3 4a1 1 0 0 1 1-1h3.5a1 1 0 0 1 1 1c0 1.25.2 2.45.57 3.57a1 1 0 0 1-.25 1z"/></svg>
      (555) 555-0142
    </p>
  </div>

  <div class="offer">
    <p class="offer__amount">UP TO <span class="accent">&amp;6000</span></p>
    <p class="offer__label">SAME DAY ADVANCE</p>
  </div>

  <p class="footnote">
    <span>FREE ESTIMATES!</span>
    <span class="footnote__divider"></span>
    <span>ON APPROVED TAX RETURNS!</span>
  </p>
</section>

<section class="card card--back">
  <div class="back-top"></div>
  <div class="back-rule"></div>
  <div class="back-bottom"></div>
  <p class="headline headline--file">FILE YOUR</p>
  <p class="headline headline--taxes">TAXES HERE</p>
  <p class="headline headline--amount">UP TO &amp;6000</p>
  <p class="headline headline--advance">SAME DAY ADVANCE</p>
</section>

</body>
</html>
```